Modern business card design for professional copywriter

I'd like a business card design that I can use to have my cards printed out by quillprint.com as a squared corners business card (see artwork and design guidelines here: https://help.quillprint.com/hc/en-gb/sections/200570950-QUILL-Product-Templates)

The design should be clean and modern and reflect the colours, tone and branding on my website: https://tessavorrin.com.au

Target Market(s)

Professionals, B2B small business owners

Industry/Entity Type

Business

Contact Information for Business Card

Tessa Vorrin
m: 0468 905 327
e: tessa@tessavorrin.com.au
w: tessavorrin.com.au

Font styles to use
Sans Serif

Requirements
Must have
• Tagline: "Smart copywriting for clever business people"
• Brand colours: fd8000, 009984, 666666 and black
Nice to have

```html
<!DOCTYPE html>
<html lang="en">
<head>
<meta charset="utf-8">
<title>Tessa Vorrin – Business Card</title>
<link href="https://fonts.googleapis.com/css2?family=Jost:wght@400;500&family=Oswald:wght@500&display=swap" rel="stylesheet">
<style>
  :root {
    --orange: #fd8000;
    --teal: #009984;
    --grey: #666666;
    --card: #1b1b1b;
    --white: #f4f4f4;
    --backdrop: #ece9e3;
  }
  * { margin: 0; padding: 0; box-sizing: border-box; }
  html, body { width: 1200px; height: 929px; overflow: hidden; }
  body {
    background: var(--backdrop);
    font-family: "Jost", sans-serif;
    display: flex;
    align-items: center;
    justify-content: center;
    gap: 60px;
  }
  .card {
    position: relative;
    width: 520px;
    height: 336px;
    background: var(--card);
    color: var(--white);
    box-shadow: 0 4px 14px rgba(0,0,0,0.18);
  }
  .card-front {
    display: flex;
    align-items: center;
    justify-content: center;
  }
  .brand-name {
    display: flex;
    align-items: center;
    gap: 12px;
    font-family: "Jost", sans-serif;
    font-weight: 500;
    font-size: 44px;
    letter-spacing: -0.5px;
  }
  .brand-mark {
    width: 16px;
    height: 16px;
    border-radius: 50%;
    background: currentColor;
  }
  .card-front .brand-name { color: var(--white); }
  .card-back .brand-name {
    position: absolute;
    top: 58px;
    left: 0;
    right: 0;
    justify-content: center;
    font-size: 34px;
    color: var(--teal);
  }
  .card-back .brand-mark { background: var(--orange); width: 13px; height: 13px; }
  .details {
    position: absolute;
    top: 150px;
    left: 0;
    right: 0;
    display: flex;
    justify-content: center;
    align-items: center;
    gap: 20px;
  }
  .identity { text-align: right; }
  .person-name {
    font-family: "Oswald", sans-serif;
    font-weight: 500;
    font-size: 30px;
    line-height: 1;
    color: var(--orange);
    letter-spacing: 0.5px;
  }
  .person-role {
    font-size: 17px;
    color: var(--white);
    margin-top: 2px;
  }
  .divider {
    width: 1.5px;
    height: 70px;
    background: var(--teal);
  }
  .contact-list { list-style: none; font-size: 14px; line-height: 1.55; letter-spacing: 0.3px; }
  .contact-list li { display: flex; align-items: center; gap: 9px; }
  .contact-list svg { width: 11px; height: 11px; flex: none; }
  .tagline {
    position: absolute;
    bottom: 36px;
    left: 0;
    right: 0;
    text-align: center;
    font-size: 14px;
    letter-spacing: 0.4px;
  }
</style>
</head>
<body>
  <section class="card card-front" aria-label="Card front">
    <div class="brand-name"><span class="brand-mark"></span>Tessa Vorrin</div>
  </section>

  <section class="card card-back" aria-label="Card back">
    <div class="brand-name"><span class="brand-mark"></span>Tessa Vorrin</div>

    <div class="details">
      <div class="identity">
        <div class="person-name">TESSA VORRIN</div>
        <div class="person-role">Copywriter</div>
      </div>
      <div class="divider"></div>
      <ul class="contact-list">
        <li>
          <svg viewBox="0 0 12 12" aria-hidden="true"><rect x="3" y="0.5" width="6" height="11" rx="1" fill="none" stroke="var(--orange)" stroke-width="1.2"/><circle cx="6" cy="9.5" r="0.7" fill="var(--orange)"/></svg>
          0468 905 327
        </li>
        <li>
          <svg viewBox="0 0 12 12" aria-hidden="true"><rect x="0.5" y="2.5" width="11" height="7" fill="var(--orange)"/><path d="M0.5 2.5 L6 7 L11.5 2.5" fill="none" stroke="var(--card)" stroke-width="1"/></svg>
          tessa@tessavorrin.com.au
        </li>
        <li>
          <svg viewBox="0 0 12 12" aria-hidden="true"><circle cx="5" cy="5" r="3.5" fill="none" stroke="var(--orange)" stroke-width="1.5"/><line x1="7.6" y1="7.6" x2="11" y2="11" stroke="var(--orange)" stroke-width="1.8"/></svg>
          tessavorrin.com.au
        </li>
      </ul>
    </div>

    <p class="tagline">Smart copywriting for clever business people</p>
  </section>
</body>
</html>
```